New Business Card Design Project

We require a business card design for Vexalund, a newly established Indian company.
Our focus is on the development, manufacturing, and export of a diverse array of pharmaceutical products on a global scale. The card should convey a professional appearance, as our primary markets are in Africa, China, and Southeast Asian nations.
We envision a two-sided business card, with the reverse side dedicated to a logo set against a solid color or an elegantly designed pattern. The corners should be rounded. We would appreciate seeing both horizontal and vertical design options. We trust the designer to utilize their expertise in creating this design.

The content for the business card is included in the attached Word file.

Target Market(s)

Our primary markets are in Africa, China, and Southeast Asian, Latin America, Maldives, Sri Lanka

Industry/Entity Type

Pharmaceutical Manufacturing and Export

Contact Information for Business Card

Colors

Designer to choose colors to be used in the design.

Requirements
Must have
• The reverse side of the business card features solely the logo along with the tagline, "Care for Every Day."
Should not have
• The logo should not exceed two instances, encompassing both the front and back sides of the card.

```html
<!DOCTYPE html>
<html lang="en">
<head>
<meta charset="utf-8">
<title>Vexalund Business Card</title>
<link href="https://fonts.googleapis.com/css2?family=Montserrat:wght@300;400;700&family=Open+Sans:wght@400&display=swap" rel="stylesheet">
<style>
  :root {
    --brand-blue: #2ea6df;
    --accent-red: #ef5f4c;
    --card-white: #ffffff;
    --ink: #1b1b1b;
    --backdrop: #222222;
  }
  html, body {
    margin: 0;
    width: 1200px;
    height: 780px;
    overflow: hidden;
    background: var(--backdrop);
  }
  .canvas {
    position: relative;
    width: 1200px;
    height: 780px;
    display: flex;
    align-items: center;
    justify-content: center;
    gap: 60px;
  }
  .card {
    position: relative;
    width: 520px;
    height: 300px;
    border-radius: 22px;
    overflow: hidden;
  }
  .card-front { background: var(--card-white); }
  .card-back { background: var(--brand-blue); }

  .front-band {
    position: absolute;
    inset: 0;
    width: 520px;
    height: 300px;
  }

  .holder {
    position: absolute;
    left: 38px;
    top: 46px;
    font-family: "Montserrat", sans-serif;
    color: var(--brand-blue);
    text-align: right;
  }
  .holder-name {
    margin: 0;
    font-size: 23px;
    font-weight: 300;
    letter-spacing: 0.3px;
  }
  .holder-name strong { font-weight: 700; }
  .holder-role {
    margin: 4px 0 0;
    font-family: "Open Sans", sans-serif;
    font-size: 12px;
    color: var(--ink);
  }

  .brand-front {
    position: absolute;
    left: 300px;
    top: 58px;
    display: flex;
    align-items: center;
    gap: 8px;
    font-family: "Montserrat", sans-serif;
    font-weight: 700;
    font-size: 32px;
    color: var(--brand-blue);
  }
  .brand-dot {
    width: 12px;
    height: 12px;
    border-radius: 50%;
    background: var(--brand-blue);
  }

  .divider {
    position: absolute;
    left: 222px;
    top: 108px;
    width: 1px;
    height: 68px;
    background: var(--brand-blue);
  }

  .contact-list {
    position: absolute;
    left: 236px;
    top: 108px;
    margin: 0;
    padding: 0;
    list-style: none;
    font-family: "Open Sans", sans-serif;
    font-size: 13px;
    color: var(--ink);
  }
  .contact-list li {
    display: flex;
    align-items: center;
    gap: 8px;
    height: 22px;
  }
  .contact-list svg { width: 13px; height: 13px; flex: none; }

  .address {
    position: absolute;
    left: 40px;
    bottom: 30px;
    margin: 0;
    font-family: "Open Sans", sans-serif;
    font-size: 12.5px;
    color: var(--card-white);
  }

  .brand-back {
    position: absolute;
    left: 0;
    right: 0;
    top: 112px;
    display: flex;
    align-items: center;
    justify-content: center;
    gap: 12px;
    font-family: "Montserrat", sans-serif;
    font-weight: 700;
    font-size: 48px;
    color: var(--card-white);
  }
  .brand-back .brand-dot {
    width: 16px;
    height: 16px;
    background: var(--card-white);
  }
  .tagline {
    position: absolute;
    left: 128px;
    top: 186px;
    margin: 0;
    font-family: "Montserrat", sans-serif;
    font-weight: 400;
    font-size: 12px;
    color: var(--card-white);
  }
</style>
</head>
<body>
<main class="canvas">
  <section class="card card-front" aria-label="Card front">
    <svg class="front-band" viewBox="0 0 520 300" aria-hidden="true">
      <path d="M0 196 Q250 262 520 204 L520 300 L0 300 Z" fill="var(--brand-blue)"/>
      <path d="M8 178 Q250 250 500 196" fill="none" stroke="var(--accent-red)" stroke-width="3" stroke-linecap="round"/>
    </svg>

    <div class="holder">
      <p class="holder-name"><strong>Arvind</strong> K. Solanke</p>
      <p class="holder-role">CEO</p>
    </div>

    <div class="brand-front">
      <span class="brand-dot"></span>
      <span>Vexalund</span>
    </div>

    <div class="divider"></div>

    <ul class="contact-list">
      <li>
        <svg viewBox="0 0 14 14" aria-hidden="true"><rect x="1.5" y="1.5" width="11" height="11" fill="none" stroke="var(--accent-red)" stroke-width="1.5"/></svg>
        +919 431570826
      </li>
      <li>
        <svg viewBox="0 0 14 14" aria-hidden="true"><circle cx="7" cy="7" r="6" fill="var(--brand-blue)"/><path d="M1 7 H13 M7 1 Q3 7 7 13 M7 1 Q11 7 7 13" fill="none" stroke="#fff" stroke-width="0.8"/></svg>
        www.vexalund.com
      </li>
      <li>
        <svg viewBox="0 0 14 14" aria-hidden="true"><rect x="1" y="3" width="12" height="9" rx="1" fill="var(--accent-red)"/><path d="M1.5 3.5 L7 8 L12.5 3.5" fill="none" stroke="#fff" stroke-width="1"/></svg>
        asolanke@vexalund.com
      </li>
    </ul>

    <p class="address">12, Nilgiri Colony, Wardha, 442001, India</p>
  </section>

  <section class="card card-back" aria-label="Card back">
    <div class="brand-back">
      <span class="brand-dot"></span>
      <span>Vexalund</span>
    </div>
    <p class="tagline">Care for Every Day.</p>
  </section>
</main>
</body>
</html>
```